Vetern Mailer for Mortgage Refinance

Hello, I need some options in my KB mailers we send out here in the USA! A sample of our mailer has been included. I need all the verbiage the same. The data merge points need to stay on too. Please make this pop. We have a high end PELDO printer and a Z auto folding machine. Letter goes into a number 10 envelope with windows. So lets see what you can do. One with colors below is our company colors and then one black, white, gray.
Blue - 3399FF------ R 51 G 153 B 255
Orange - FF9933----- R 255 G 153 B 51
Black – 333333------ R 51 G 51 B 51
White – FFFFFF------ R 255 G 255 B 255

Target Market(s)

United States Military Service Members

Industry/Entity Type

Mortgage Lender

Requirements
Must have
• Margins for folding with Z and Number 10 Envelope with two windows

```html
<!DOCTYPE html>
<html lang="en">
<head>
<meta charset="utf-8">
<title>Summit Crest Home Loans – KB Refinance Mailer</title>
<link href="https://fonts.googleapis.com/css2?family=Montserrat:wght@400;500;600;700;800&display=swap" rel="stylesheet">
<style>
:root{
  --blue:#3399ff;
  --blue-deep:#1f6fd1;
  --orange:#ff9933;
  --ink:#333333;
  --white:#ffffff;
  --stage:#e4e6e9;
}
*{box-sizing:border-box;margin:0;padding:0}
html,body{width:1200px;height:2400px;overflow:hidden}
body{background:var(--stage);font-family:"Montserrat",Arial,sans-serif;color:var(--ink);position:relative}
.sheet{position:absolute;left:170px;width:860px;height:1113px;background:var(--white);box-shadow:0 6px 22px rgba(0,0,0,.12);overflow:hidden}
.sheet--front{top:50px}
.sheet--back{top:1237px}
.abs{position:absolute}

/* address panel */
.field{position:absolute;left:44px;height:20px;border:1.5px solid var(--blue);border-radius:3px;display:flex;align-items:stretch;font-size:12px}
.field__label{background:var(--blue);color:var(--white);padding:0 12px;display:flex;align-items:center;font-weight:500}
.field--re{top:41px;width:201px}
.field--loan{top:66px;width:296px}
.disclaim{left:44px;top:115px;width:320px;font-size:13.5px;line-height:1.3;font-weight:500}
.merge{left:44px;top:223px;font-size:15px;line-height:1.3;letter-spacing:.4px}
.offer{left:549px;top:41px;width:269px;height:145px;border:2px solid var(--orange);border-radius:10px;padding:8px 14px}
.pill{height:22px;border:1.5px solid var(--blue);border-radius:5px;font-size:13px;display:flex;align-items:center;justify-content:center;margin-bottom:7px}
.offer__amount{text-align:center;font-size:50px;font-weight:800;line-height:1;margin-top:8px}
.defer{left:549px;top:195px;width:269px;text-align:center;font-size:13px;line-height:1.3}
.toll{left:549px;top:254px;width:269px;text-align:center}
.toll__label{color:var(--blue);font-size:21px;font-weight:500}
.toll__label b{font-weight:700}
.toll__phone{font-size:24px;font-weight:800;display:flex;align-items:center;justify-content:center;gap:6px;margin-top:2px}
.toll__hours{font-size:14px;margin-top:10px}

/* letter panel */
.brand{font-weight:500;color:var(--blue);letter-spacing:2px;display:flex;align-items:center;gap:10px;white-space:nowrap}
.brand__dot{width:12px;height:12px;border-radius:50%;background:var(--orange);flex:none}
.brand--lead{left:46px;top:408px;font-size:36px}
.salute{left:46px;top:484px;font-size:16px}
.salute b{font-weight:700}
.body-copy{left:46px;top:516px;width:400px;font-size:10.4px;line-height:1.32}
.body-copy sup{font-size:7px}
.callout{left:46px;top:645px;width:380px;color:var(--blue);font-size:17.5px;font-weight:700;line-height:1.2}
.callout sup{font-size:10px}
.photo{left:0;top:400px;width:860px;height:340px;clip-path:polygon(541px 12px,860px 12px,860px 333px,445px 333px);background:linear-gradient(135deg,#e8edf3 0%,#c7d3e0 45%,#9db3c9 75%,#d9e2ec 100%)}

/* benefits panel */
.benefits{left:54px;top:772px}
.benefits h3{font-size:18.5px;font-weight:700;margin-bottom:8px}
.benefits h3.irrrl{margin-top:14px}
.benefits ul{list-style:none}
.benefits li{font-size:11.6px;line-height:19px;display:flex;align-items:center;gap:7px}
.note{left:50px;top:1076px;font-size:11px;font-style:italic}
.banner{left:0;top:0;width:860px;height:1113px;pointer-events:none}
.banner__text{left:432px;top:796px;width:415px;color:var(--white);font-size:11.4px;line-height:1.35}
.brand--foot{left:371px;top:916px;font-size:18px;letter-spacing:1px;gap:8px}
.brand--foot .brand__dot{width:10px;height:10px}
.minifield{position:absolute;left:588px;width:230px;height:19px;border:1.5px solid var(--blue);border-radius:3px;font-size:10px;display:flex}
.minifield span{background:var(--blue);color:var(--white);padding:0 8px;display:flex;align-items:center;gap:4px}
.cashout{left:371px;top:967px;font-size:17px;font-weight:700}
.cashout em{font-style:normal;color:var(--blue)}
.company{left:378px;top:1018px;font-size:13px;line-height:1.3}
.company b{font-weight:700;font-size:13.5px}
.company__addr{display:flex;gap:6px;align-items:flex-start}
.nmls{left:674px;top:1020px;width:140px;font-weight:700;font-size:14px;color:var(--white)}
.nmls__tag{background:var(--blue);display:inline-block;padding:1px 10px;margin-bottom:4px}
.nmls__num{background:var(--orange);padding:1px 6px}

/* back sheet */
.fine{left:46px;top:349px;width:774px;font-size:8.6px;line-height:1.28}
.fine p{margin-bottom:7px}
.fine .lead{font-weight:700}
.fine h4{color:var(--blue);font-size:8.6px;font-weight:700;margin-bottom:1px}
</style>
</head>
<body>

<section class="sheet sheet--front" aria-label="Mailer front">
  <!-- top third: envelope window panel -->
  <div class="field field--re"><span class="field__label">RE:</span></div>
  <div class="field field--loan"><span class="field__label">Loan ID Number</span></div>
  <p class="abs disclaim">Summit Crest Home Loans LLC Is not affiliated with your current lender nor is it an agency of the Federal Government.</p>
  <p class="abs merge">&lt;&lt;first_name&gt;&gt; &lt;&lt;last_name&gt;&gt;<br>&lt;&lt;address&gt;&gt;<br>&lt;&lt;city_state_zip&gt;&gt;</p>

  <div class="abs offer">
    <div class="pill">Close_month</div>
    <div class="pill">Skip_month</div>
    <div class="offer__amount">$0</div>
  </div>
  <p class="abs defer">You may be able to defer<br>your next two payments.<sup>1</sup></p>
  <div class="abs toll">
    <div class="toll__label">Call <b>Toll Free</b></div>
    <div class="toll__phone">
      <svg width="18" height="18" viewBox="0 0 20 20"><circle cx="10" cy="10" r="9" fill="none" stroke="#ff9933" stroke-width="2"/><path d="M7 5.5l2 2.2-1.2 1.3a6 6 0 0 0 3.2 3.2l1.3-1.2 2.2 2-1.4 1.6C9.6 14.3 5.7 10.4 5.4 6.9z" fill="#ff9933"/></svg>
      555 0142 7730
    </div>
    <div class="toll__hours">Weekdays 6 a.m. to 5 p.m. PST</div>
  </div>

  <!-- middle third: letter -->
  <div class="abs photo" role="img" aria-label="Photo of a hand holding a small model house and keys in front of a home"></div>
  <svg class="abs banner" viewBox="0 0 860 1113" aria-hidden="true">
    <line x1="541" y1="408" x2="860" y2="408" stroke="#ff9933" stroke-width="3"/>
    <line x1="541" y1="408" x2="445" y2="733" stroke="#3399ff" stroke-width="3"/>
    <line x1="528" y1="425" x2="432" y2="733" stroke="#ff9933" stroke-width="1.5"/>
    <line x1="0" y1="736" x2="445" y2="736" stroke="#3399ff" stroke-width="3"/>
    <polygon points="420,780 860,780 860,866 395,866" fill="#3399ff"/>
    <line x1="395" y1="869" x2="860" y2="869" stroke="#ff9933" stroke-width="3"/>
  </svg>
  <div class="abs brand brand--lead"><span class="brand__dot"></span>SUMMIT CREST</div>
  <p class="abs salute">Dear <b>Marcus,</b></p>
  <p class="abs body-copy">We are contacting you regarding your &lt;&lt;balance&gt;&gt; KB loan. Our review has indicated that because of homes appreciating in &lt;&lt;city&gt;&gt;, you may now qualify for additional benefits. These benefits may include lowering your monthly mortgage payment, deferring up to two payments, refund of escrow, and $35,000 or more cash-out.<sup>3</sup> Call our KB Program Specialist at &lt;&lt;phone_number&gt;&gt; at your earliest convenience to receive a detailed explanation of how you may be able to access these benefits.<sup>4</sup></p>
  <p class="abs callout">You may also receive a check back from your escrow account.<sup>2</sup></p>

  <!-- bottom third: benefits -->
  <div class="abs benefits">
    <h3>Additional Benefits Include:</h3>
    <ul>
      <li><svg width="11" height="11" viewBox="0 0 12 12"><rect x="0.75" y="0.75" width="10.5" height="10.5" rx="2" fill="none" stroke="#ff9933" stroke-width="1.5"/><path d="M3 6l2 2 4-4.5" fill="none" stroke="#ff9933" stroke-width="1.6"/></svg>100% LTV Cash-Out Available</li>
      <li><svg width="11" height="11" viewBox="0 0 12 12"><rect x="0.75" y="0.75" width="10.5" height="10.5" rx="2" fill="none" stroke="#ff9933" stroke-width="1.5"/><path d="M3 6l2 2 4-4.5" fill="none" stroke="#ff9933" stroke-width="1.6"/></svg>Pay off High Interest Debt</li>
      <li><svg width="11" height="11" viewBox="0 0 12 12"><rect x="0.75" y="0.75" width="10.5" height="10.5" rx="2" fill="none" stroke="#ff9933" stroke-width="1.5"/><path d="M3 6l2 2 4-4.5" fill="none" stroke="#ff9933" stroke-width="1.6"/></svg>Complete a long overdue home renovation</li>
      <li><svg width="11" height="11" viewBox="0 0 12 12"><rect x="0.75" y="0.75" width="10.5" height="10.5" rx="2" fill="none" stroke="#ff9933" stroke-width="1.5"/><path d="M3 6l2 2 4-4.5" fill="none" stroke="#ff9933" stroke-width="1.6"/></svg>No out-of-pocket appraisal deposit</li>
      <li><svg width="11" height="11" viewBox="0 0 12 12"><rect x="0.75" y="0.75" width="10.5" height="10.5" rx="2" fill="none" stroke="#ff9933" stroke-width="1.5"/><path d="M3 6l2 2 4-4.5" fill="none" stroke="#ff9933" stroke-width="1.6"/></svg>No Private Mortgage Insurance</li>
    </ul>
    <h3 class="irrrl">KB IRRRL Benefits</h3>
    <ul>
      <li><svg width="11" height="11" viewBox="0 0 12 12"><rect x="0.75" y="0.75" width="10.5" height="10.5" rx="2" fill="none" stroke="#3399ff" stroke-width="1.5"/><path d="M3 6l2 2 4-4.5" fill="none" stroke="#3399ff" stroke-width="1.6"/></svg>Reduce Your Current Interest Rate</li>
      <li><svg width="11" height="11" viewBox="0 0 12 12"><rect x="0.75" y="0.75" width="10.5" height="10.5" rx="2" fill="none" stroke="#3399ff" stroke-width="1.5"/><path d="M3 6l2 2 4-4.5" fill="none" stroke="#3399ff" stroke-width="1.6"/></svg>Mortgage-Only Credit Report</li>
      <li><svg width="11" height="11" viewBox="0 0 12 12"><rect x="0.75" y="0.75" width="10.5" height="10.5" rx="2" fill="none" stroke="#3399ff" stroke-width="1.5"/><path d="M3 6l2 2 4-4.5" fill="none" stroke="#3399ff" stroke-width="1.6"/></svg>No Appraisal Required</li>
      <li><svg width="11" height="11" viewBox="0 0 12 12"><rect x="0.75" y="0.75" width="10.5" height="10.5" rx="2" fill="none" stroke="#3399ff" stroke-width="1.5"/><path d="M3 6l2 2 4-4.5" fill="none" stroke="#3399ff" stroke-width="1.6"/></svg>Fast Closings in 8-14 days</li>
      <li><svg width="11" height="11" viewBox="0 0 12 12"><rect x="0.75" y="0.75" width="10.5" height="10.5" rx="2" fill="none" stroke="#3399ff" stroke-width="1.5"/><path d="M3 6l2 2 4-4.5" fill="none" stroke="#3399ff" stroke-width="1.6"/></svg>No Income or Asset Verification Required</li>
    </ul>
  </div>
  <p class="abs note">*Please see reverse for disclaimer</p>

  <p class="abs banner__text">We recommend you call our office at &lt;&lt;phone_number&gt;&gt; within the next 3-5 business days as market rates fluctuate. By taking action now your next mortgage payment may not be due until &lt;&lt;next_pay_month&gt;&gt;.2 To avoid further delay, please call today.</p>
  <div class="abs brand brand--foot"><span class="brand__dot"></span>SUMMIT CREST</div>
  <div class="minifield" style="top:911px"><span>Phone:
    <svg width="10" height="10" viewBox="0 0 20 20"><circle cx="10" cy="10" r="9" fill="#ff9933"/><path d="M7 5.5l2 2.2-1.2 1.3a6 6 0 0 0 3.2 3.2l1.3-1.2 2.2 2-1.4 1.6C9.6 14.3 5.7 10.4 5.4 6.9z" fill="#fff"/></svg></span></div>
  <div class="minifield" style="top:935px"><span>Loan ID Number:</span></div>
  <p class="abs cashout">CASH OUT OPTIONS (TAX FREE): <em>$35,000 OR MORE</em></p>
  <div class="abs company">
    <b>Summit Crest Home Loans LLC</b>
    <div class="company__addr">
      <svg width="12" height="16" viewBox="0 0 12 16"><path d="M6 0.8A5 5 0 0 0 1 5.8c0 3.8 5 9.4 5 9.4s5-5.6 5-9.4A5 5 0 0 0 6 .8z" fill="#ff9933"/><circle cx="6" cy="5.8" r="1.9" fill="#fff"/></svg>
      <span>4120 Canyon View Rd Ste 210<br>Mesa Verde, AZ 85000</span>
    </div>
  </div>
  <div class="abs nmls">
    <span class="nmls__tag">NMLS</span><br>
    <span class="nmls__num">0000000 00000</span>
  </div>
</section>

<section class="sheet sheet--back" aria-label="Mailer reverse with disclaimers">
  <div class="abs fine">
    <p class="lead">Offer is available only for loans made or arranged through Summit Crest Home Loans LLC, NMLS# 0000000, 4120 Canyon View Rd, Ste. 210, Mesa Verde, AZ 85000. We are not associated with, or acting on behalf of your current lender or any government agency. Verification of employment may apply. This program is exclusive to the beneficiary named above and is nontransferable.</p>
    <h4>TERMS AND CONDITIONS:</h4>
    <p>This offer is extended because you appear to satisfy certain credit criteria derived from information in a pre-screened report received from a credit reporting agency. The amount and terms of any credit offer will be determined by your credit history, your capacity to make payments and available equity in your home. The minimum loan amount shall be no less than $80,000.00. You may no longer qualify if you do not continue to meet the criteria used to select you, or if you do not furnish any required collateral. To qualify, you may be required to provide up to two years of income verification. This offer is made under the assumption that your debt-to-income ratio does not exceed 50%; other programs may be available with a higher level of debt. Credit severity may affect the down payment. The lender may also cancel this offer if it is unable to verify the information you have provided. All bankruptcies must be discharged. The lender must be in a valid first or second lien position and property hazard insurance is required. Additional information and documentation may be needed to issue loan commitment. The amount of the pre-selected new home loan is based on the current balance that is coming from the information received from one of three credit reporting agencies.</p>
    <h4>State Disclosure Requirements:</h4>
    <p>Summit Crest Home Loans LLC is a licensed mortgage lender/broker. The following states require disclosure of licensing information. If your state is not listed, it does not require a specific license disclosure: AZ Department of Insurance and Financial Institutions License #: 0000000; CA Licensed by the Department of Financial Protection and Innovation under the California Residential Mortgage Lending Act, License #: 00000000; CO Department of Regulatory Agencies License #: 0000000; FL Office of Financial Regulation License #: 000000; ID Mortgage Broker/Lender License #: 0000000; TX SML Mortgage Company License; UT Department of Commerce License #: 0000000; WA Department of Financial Institutions License #: 0000000.</p>
    <h4>1. Deferred mortgage payments:</h4>
    <p>If you do not make your mortgage payment for the month that you are closing your new loan, it may be possible to capitalize that payment into your new loan, thereby deferring the due date of your next mortgage payment to be due 1-2 months. Please be aware that deferring your payment as described may result in additional interest charges over the life of your loan. This deferred interest will be added to the principal balance of your new loan, potentially increasing your future monthly payments and the total amount payable over the term of your mortgage. Payments received after this period may attract a late fee as per the terms of your loan agreement. We encourage you to manage your payments responsibly to avoid any additional charges and to maintain a healthy credit status.</p>
    <h4>2. Escrow Account Refund (if applicable):</h4>
    <p>If you have an escrow account associated with your mortgage, please be aware that any refund from this account is governed by the terms and conditions of your current lender. The timing and amount of a potential refund depend on the account balance at the time of loan payoff, along with specific escrow requirements. For those without an escrow account, this clause does not apply. We advise all borrowers to reach out to their current lender for detailed information about their escrow account status and any refund eligibility that may pertain.</p>
    <h4>3. Example cash-out of $35,000</h4>
    <p>will be in addition to your monthly mortgage payment. Cash-out offer assumes you have adequate equity in your property. A full appraisal will be required with your loan application to determine the actual value. Your actual rate and payment may be different based on many factors. Please contact one of our Licensed Lending Officers at 555-010-4477 for a customized rate and payment quote. Cash-out offers may not be available in TX.</p>
    <h4>4. Your circumstances may vary,</h4>
    <p>so please contact 555-010-4477 to see how we may assist. Summit Crest Home Loans is an Equal Housing Lender. As prohibited by federal law, we do not engage in business practices that discriminate on the basis of race, color, religion, national origin, sex, marital status, age (provided you have the capacity to enter into a binding contract), because all or part of your income may be derived from any public assistance program, or because you have, in good faith, exercised any right under the Consumer Credit Protection Act. The federal agency that administers our compliance with these federal laws is the Federal Trade Commission, Equal Credit Opportunity, Washington, DC, 20580.</p>
  </div>
</section>

</body>
</html>
```